Lumavento business card

We need a modern business card - With our 4 colors - See web: www.lumavento.dk

I have attached logo and som old business Cards we have - Lets Make the new ones shine...:-) -

Industry/Entity Type

Business

Requirements
Must have
• the logo with lumavento only,

```html
<!DOCTYPE html>
<html lang="da">
<head>
<meta charset="utf-8">
<title>Lumavento – visitkort</title>
<link rel="stylesheet" href="https://fonts.googleapis.com/css2?family=Source+Sans+3:wght@400;700&display=swap">
<style>
  :root {
    --lime: #a5c73a;
    --magenta: #e5087e;
    --white: #ffffff;
    --ink: #3a3a3a;
    --backdrop: #e9e9e7;
  }
  html, body {
    margin: 0;
    width: 1200px;
    height: 900px;
    overflow: hidden;
    background: var(--backdrop);
    font-family: "Source Sans 3", "Myriad Pro", Arial, sans-serif;
  }
  .business-card {
    position: absolute;
    left: 100px;
    top: 150px;
    width: 1000px;
    height: 600px;
    background: var(--white);
    overflow: hidden;
    box-shadow: 0 6px 24px rgba(0,0,0,0.12);
  }
  .card-waves {
    position: absolute;
    inset: 0;
    width: 1000px;
    height: 600px;
  }
  .brand {
    position: absolute;
    left: 64px;
    top: 70px;
    width: 420px;
    text-align: center;
    color: var(--ink);
  }
  .brand-mark {
    display: block;
    width: 96px;
    height: 96px;
    margin: 0 auto 30px;
    border-radius: 50%;
    background: var(--lime);
  }
  .brand-name {
    margin: 0;
    font-size: 38px;
    font-weight: 400;
    letter-spacing: 5px;
    line-height: 1;
  }
  .brand-rule {
    height: 4px;
    background: var(--lime);
    margin: 28px 0 18px;
    border: 0;
  }
  .brand-tagline {
    margin: 0;
    font-size: 24px;
  }
  .contact {
    position: absolute;
    right: 40px;
    top: 272px;
    text-align: right;
    color: var(--white);
  }
  .contact-name {
    margin: 0;
    font-size: 35px;
    font-weight: 700;
    line-height: 1.1;
  }
  .contact-role {
    margin: 2px 0 34px;
    font-size: 25px;
  }
  .contact-list {
    list-style: none;
    margin: 0;
    padding: 0;
    font-size: 26px;
  }
  .contact-list li {
    display: flex;
    justify-content: flex-end;
    align-items: center;
    gap: 14px;
    height: 41px;
  }
  .contact-icon {
    width: 20px;
    height: 20px;
    fill: var(--white);
  }
  .company-address {
    position: absolute;
    right: 40px;
    bottom: 50px;
    margin: 0;
    color: var(--white);
    font-size: 26px;
  }
</style>
</head>
<body>
  <div class="business-card">
    <svg class="card-waves" viewBox="0 0 1000 600" aria-hidden="true">
      <path fill="var(--magenta)" d="M0,300 C150,460 320,470 470,380 S820,100 1000,225 L1000,600 L0,600 Z"/>
      <path fill="var(--white)" d="M0,322 C150,478 320,488 470,398 S820,132 1000,258 L1000,600 L0,600 Z"/>
      <path fill="var(--lime)" d="M0,334 C150,488 320,498 470,410 S820,150 1000,276 L1000,600 L0,600 Z"/>
    </svg>

    <div class="brand">
      <span class="brand-mark"></span>
      <p class="brand-name">lumavento</p>
      <hr class="brand-rule">
      <p class="brand-tagline">Medier til unge</p>
    </div>

    <div class="contact">
      <p class="contact-name">Anders Holmvik</p>
      <p class="contact-role">Salgsdirektor</p>
      <ul class="contact-list">
        <li>+45 20 41 63 87
          <svg class="contact-icon" viewBox="0 0 24 24"><path d="M6.6 10.8a15.1 15.1 0 0 0 6.6 6.6l2.2-2.2c.3-.3.7-.4 1-.2 1.1.4 2.3.6 3.6.6.6 0 1 .4 1 1V20c0 .6-.4 1-1 1C10.6 21 3 13.4 3 4c0-.6.4-1 1-1h3.5c.6 0 1 .4 1 1 0 1.3.2 2.5.6 3.6.1.3 0 .7-.2 1z"/></svg>
        </li>
        <li>ah@lumavento.dk
          <svg class="contact-icon" viewBox="0 0 24 24"><path d="M2 5h20v14H2z M3.5 6.5 12 13l8.5-6.5" stroke="var(--lime)" stroke-width="1.6"/></svg>
        </li>
        <li>www.lumavento.dk
          <svg class="contact-icon" viewBox="0 0 24 24"><circle cx="12" cy="12" r="10"/><path d="M2 12h20M12 2c3 3 3 17 0 20M12 2c-3 3-3 17 0 20" stroke="var(--lime)" stroke-width="1.5" fill="none"/></svg>
        </li>
      </ul>
    </div>

    <p class="company-address">Solsikkevej 14 - 2100 København Ø -Tlf. 35 12 48 70</p>
  </div>
</body>
</html>
```